Oil Field Service company needs professional business cards

Looking to clean up our current company business cards and look a little more professional. Brenwick Casing Services is a US based company that services the oil field. We deal with engineers, managers and oil rigs....................................................................................................................................................................................................................................................................................................................................................................................................

Target Market(s)

Oil and Gas professionals

Industry/Entity Type

Oil And Gas

Contact Information for Business Card

See attached photo as example

Font styles to use
Sans Serif

Colors
ec1f27

Requirements
Must have
• Company Logo, Name, Title, Cell, Office, Fax, Email.
• See attached photo
Nice to have
• External CRT, Internal CRT, Casing Crews, Torque Turn, Laydown Machine
Should not have
• Do not introduce any new pictures and keep it professional looking

```html
<!DOCTYPE html>
<html lang="en">
<head>
<meta charset="utf-8">
<title>Brenwick Casing Services — Business Card</title>
<link href="https://fonts.googleapis.com/css2?family=Montserrat:wght@500;600;800&family=Oswald:wght@500&display=swap" rel="stylesheet">
<style>
  :root {
    --red: #d9373b;
    --slate: #333f4b;
    --white: #ffffff;
    --stage: #e9e6e1;
    --ink: #2e3640;
  }
  * { margin: 0; padding: 0; box-sizing: border-box; }
  html, body { width: 1200px; height: 989px; overflow: hidden; }
  body {
    background: var(--stage);
    font-family: "Montserrat", Arial, sans-serif;
    display: flex;
    align-items: center;
    justify-content: center;
    gap: 80px;
  }
  .card {
    position: relative;
    width: 380px;
    height: 665px;
    background: var(--white);
    overflow: hidden;
    box-shadow: 0 10px 30px rgba(0,0,0,0.18);
  }
  .wordmark {
    position: absolute;
    display: flex;
    align-items: center;
    gap: 12px;
    color: var(--slate);
    font-weight: 800;
    text-transform: uppercase;
    line-height: 1.05;
  }
  .wordmark .dot {
    width: 22px; height: 22px;
    border-radius: 50%;
    background: var(--red);
    flex: none;
  }
  .card--front .wordmark { top: 200px; left: 0; right: 0; justify-content: center; font-size: 34px; }
  .services {
    position: absolute;
    top: 312px; left: 0; right: 0;
    text-align: center;
    font-size: 10.5px;
    font-weight: 500;
    color: var(--ink);
    letter-spacing: 0.4px;
    line-height: 1.6;
    text-transform: uppercase;
  }
  .badges {
    position: absolute;
    bottom: 40px; right: 36px;
    display: flex; gap: 12px; align-items: flex-end;
  }
  .badge { background: #c9c9c9; }
  .badge--round { width: 40px; height: 40px; border-radius: 50%; border: 3px solid var(--red); background: none; }
  .badge--wide { width: 44px; height: 22px; background: #444; }
  .badge--square { width: 30px; height: 34px; background: #222; }

  .card--back .wordmark { top: 70px; left: 150px; font-size: 22px; }
  .back-shape { position: absolute; inset: 0; }
  .contact {
    position: absolute;
    left: 34px; top: 330px;
    color: var(--white);
  }
  .contact .name {
    font-family: "Oswald", Arial, sans-serif;
    font-weight: 500;
    font-size: 34px;
    letter-spacing: 0.5px;
    text-transform: uppercase;
    line-height: 1;
  }
  .contact .title {
    font-family: "Oswald", Arial, sans-serif;
    font-weight: 500;
    font-size: 16px;
    letter-spacing: 1px;
    text-transform: uppercase;
    margin-top: 4px;
  }
  .address { margin-top: 26px; font-size: 13px; font-weight: 500; line-height: 1.5; }
  .lines { list-style: none; margin-top: 6px; font-size: 13px; font-weight: 500; }
  .lines li { display: flex; align-items: center; gap: 10px; height: 22px; }
  .icon {
    width: 18px; height: 18px; border-radius: 4px;
    background: var(--white);
    display: flex; align-items: center; justify-content: center;
    flex: none;
  }
  .icon svg { width: 12px; height: 12px; fill: var(--red); }
</style>
</head>
<body>

<section class="card card--front">
  <div class="wordmark"><span class="dot"></span><span>Brenwick<br>Casing Services</span></div>
  <p class="services">External CRT - Internal CRT - Casing Crews<br>Torque Turn - Laydown Machine</p>
  <div class="badges">
    <span class="badge badge--round"></span>
    <span class="badge badge--wide"></span>
    <span class="badge badge--square"></span>
  </div>
</section>

<section class="card card--back">
  <svg class="back-shape" viewBox="0 0 380 665" preserveAspectRatio="none">
    <path d="M0,150 Q260,190 370,560 L380,600 L380,665 L0,665 Z" fill="var(--slate)"/>
    <path d="M0,205 Q250,250 345,600 L360,665 L0,665 Z" fill="var(--red)"/>
    <path d="M0,128 Q285,170 380,520" fill="none" stroke="var(--slate)" stroke-width="2"/>
  </svg>
  <div class="wordmark"><span class="dot"></span><span>Brenwick<br>Casing Services</span></div>

  <div class="contact">
    <h1 class="name">Cody Harlan</h1>
    <p class="title">Area Manager</p>
    <p class="address">4120 Ridgeline Parkway<br>Granbury, TX 76048</p>
    <ul class="lines">
      <li><span class="icon"><svg viewBox="0 0 24 24"><path d="M6.6 10.8a15 15 0 0 0 6.6 6.6l2.2-2.2a1 1 0 0 1 1-.25 11.4 11.4 0 0 0 3.6.57 1 1 0 0 1 1 1V20a1 1 0 0 1-1 1A17 17 0 0 1 3 4a1 1 0 0 1 1-1h3.5a1 1 0 0 1 1 1c0 1.25.2 2.46.57 3.6a1 1 0 0 1-.25 1z"/></svg></span>(555) 214 - 3800</li>
      <li><span class="icon"><svg viewBox="0 0 24 24"><path d="M7 1h10a2 2 0 0 1 2 2v18a2 2 0 0 1-2 2H7a2 2 0 0 1-2-2V3a2 2 0 0 1 2-2zm0 3v14h10V4z"/></svg></span>(555) 419 - 2261</li>
      <li><span class="icon"><svg viewBox="0 0 24 24"><path d="M6 2h10v5H6zM3 8h18a1 1 0 0 1 1 1v8h-4v5H6v-5H2V9a1 1 0 0 1 1-1zm5 8v4h8v-4z"/></svg></span>(555) 214 - 3390</li>
      <li><span class="icon"><svg viewBox="0 0 24 24"><path d="M12 2a10 10 0 1 0 0 20 10 10 0 0 0 0-20zm6.9 9h-3a15 15 0 0 0-1.3-6 8 8 0 0 1 4.3 6zM12 4c1 1.3 1.8 3.9 1.9 7h-3.8C10.2 7.9 11 5.3 12 4zM9.4 5a15 15 0 0 0-1.3 6h-3a8 8 0 0 1 4.3-6zM5.1 13h3a15 15 0 0 0 1.3 6 8 8 0 0 1-4.3-6zM12 20c-1-1.3-1.8-3.9-1.9-7h3.8c-.1 3.1-.9 5.7-1.9 7zm2.6-1a15 15 0 0 0 1.3-6h3a8 8 0 0 1-4.3 6z"/></svg></span>www.brenwickcasing.com</li>
      <li><span class="icon"><svg viewBox="0 0 24 24"><path d="M2 5h20v14H2zm2 2v.5l8 5 8-5V7zm0 3v7h16v-7l-8 5z"/></svg></span>cody@brenwickcasing.com</li>
    </ul>
  </div>
</section>

</body>
</html>
```